Rovelux

Hi everyone!

Looks like our project is more sophisticated than we expected. So good news - we increased the budget! and one of you will sure get the prize - no money back for us!

We are a young Russian company that specializes in in-taxi entertainment. We believe that our key strength is great attention to user experience. We've devoted much effort to improve ergonomics of our devices - tablet PCs that we install in the taxis. And yes, we enjoy to simplify things!

Now we need the most basic things - a logo and some staff for client meetings (primarily advertisers and ad agencies).

As for logo - we already have one engraved on the prototypes of our device (see attached file). This is one of the ideas (still far from perfect) - what we appreciate in it is minimalistic yet stylish approach.

As for "take it to the meeting stuff" we want to start with name card, pen and notepad (A4) that we will leave in clients's office, also as a reminder. Shall your have more smart ideas - always welcome!

As for logo and name cards - we would like to make an image of serious but modern company. Our design should communicate creativity and reliability. We believe that "to understand is to simplify" - minimalistic design is the most difficult one. Its better to work hard on fonts and arrangement, than put 10 variegated images.

SO THE TASK IS TO DESIGN:
- a logo
- a name card
- a note pad (great example in attachment)
- a pen

Shall you have more questions - please ask in comments.

We look forward to meeting like-minded fellows here!
Updates

Target Market(s)

Out target are:

- advertiser
- advertising agencies
- taxi passenger

Industry/Entity Type

It Company

Requirements
Must have
• font should be chosen very carefully
Nice to have
• classic minimalistic plain text only but very stylish name card is a dream of one of our co-founders:)
Should not have
• we do not want to have taxi-like colors and chess-boards. We are closer to "innovation", "entertainment", and "user experience", rather than "taxi".

```html
<!DOCTYPE html>
<html lang="en">
<head>
<meta charset="utf-8">
<title>Rovelux — Name Card</title>
<link rel="stylesheet" href="https://fonts.googleapis.com/css2?family=Alegreya:wght@400;500&display=swap">
<style>
  :root {
    --page-bg: #ffffff;
    --card-bg: #ffffff;
    --ink: #4e7189;
    --accent: #9a8592;
    --shadow: rgba(0, 0, 0, 0.22);
  }
  html, body {
    margin: 0;
    padding: 0;
    width: 1200px;
    height: 1000px;
    overflow: hidden;
    background: var(--page-bg);
  }
  .canvas {
    position: relative;
    width: 1200px;
    height: 1000px;
    font-family: "Alegreya", Georgia, serif;
    color: var(--ink);
  }
  .card {
    position: absolute;
    left: 100px;
    top: 175px;
    width: 1002px;
    height: 650px;
    background: var(--card-bg);
    border-radius: 100px;
    box-shadow: 0 0 6px 1px var(--shadow);
  }
  .holder {
    position: absolute;
    left: 0;
    right: 0;
    text-align: center;
  }
  .holder-name {
    top: 92px;
    font-size: 31px;
    letter-spacing: 1.6px;
    line-height: 1;
  }
  .holder-role {
    top: 134px;
    font-size: 24px;
    letter-spacing: 1.2px;
    line-height: 1;
  }
  .wordmark {
    position: absolute;
    left: 0;
    right: 0;
    top: 262px;
    text-align: center;
    font-size: 96px;
    font-weight: 500;
    letter-spacing: 1px;
    line-height: 1;
  }
  .chevron {
    position: absolute;
    top: 293px;
    width: 38px;
    height: 62px;
  }
  .chevron-left { left: 44px; }
  .chevron-right { right: 46px; }
  .chevron path {
    fill: none;
    stroke: var(--accent);
    stroke-width: 6;
    stroke-linecap: butt;
    stroke-linejoin: miter;
  }
  .contacts {
    position: absolute;
    left: 0;
    right: 0;
    top: 451px;
    margin: 0;
    text-align: center;
    font-style: normal;
    font-size: 26px;
    letter-spacing: 1px;
    line-height: 31.5px;
  }
  .contacts span { display: block; }
</style>
</head>
<body>
<div class="canvas">
  <section class="card">
    <div class="holder holder-name">Dmitry Kovalenko</div>
    <div class="holder holder-role">Co-founder and CEO</div>

    <svg class="chevron chevron-left" viewBox="0 0 38 62" aria-hidden="true">
      <path d="M35 3 L5 31 L35 59"/>
    </svg>
    <div class="wordmark">Rovelux</div>
    <svg class="chevron chevron-right" viewBox="0 0 38 62" aria-hidden="true">
      <path d="M3 3 L33 31 L3 59"/>
    </svg>

    <address class="contacts">
      <span>123456, Moscow</span>
      <span>Lesnaya str. 21/7, bldg. 3, office 5</span>
      <span>+7 900 555 0147; +7 495 555 0183</span>
      <span>kovalenko@rovelux.com</span>
      <span>www.rovelux.com</span>
    </address>
  </section>
</div>
</body>
</html>
```